business card for a massage therapy practice named 'Cedar and Willow Massage Studio'

I really need a trendy, yet easy on the eyes business card to complement my logo. Ideally with some gold or rose gold foil work.

My uploaded file of the logo I have in horizontal but I have a vertical version as well. Another color that is used in the website is a blush pink here and there. I'd like to see some trendy tropical leaves in the design.

```html
<!DOCTYPE html>
<html lang="en">
<head>
<meta charset="UTF-8">
<title>Cedar and Willow Massage Studio – Business Card</title>
<link href="https://fonts.googleapis.com/css2?family=Roboto:wght@400;500&display=swap" rel="stylesheet">
<style>
  :root {
    --backdrop: #ecebe8;
    --card: #faf9f7;
    --card-edge: #e4e2de;
    --foil: #c49a72;
    --foil-soft: #d1ae8c;
  }
  * { margin: 0; padding: 0; box-sizing: border-box; }
  html, body {
    width: 966px;
    height: 1200px;
    overflow: hidden;
    background: var(--backdrop);
    font-family: "Roboto", Arial, sans-serif;
  }
  .canvas {
    position: relative;
    width: 966px;
    height: 1200px;
  }
  .card {
    position: absolute;
    left: 193px;
    width: 580px;
    height: 340px;
    background: var(--card);
    border: 1px solid var(--card-edge);
    box-shadow: 0 2px 6px rgba(0,0,0,0.06);
    color: var(--foil);
  }
  .card--front { top: 150px; }
  .card--back { top: 740px; }

  /* Front */
  .front-brand {
    position: absolute;
    left: 40px;
    top: 0;
    width: 260px;
    height: 100%;
    display: flex;
    align-items: center;
    gap: 12px;
  }
  .brand-dot {
    flex: none;
    width: 26px;
    height: 26px;
    border-radius: 50%;
    background: var(--foil-soft);
  }
  .brand-name {
    font-size: 20px;
    font-weight: 500;
    line-height: 1.25;
    color: var(--foil);
  }
  .divider {
    position: absolute;
    left: 312px;
    top: 95px;
    width: 1px;
    height: 150px;
    background: var(--foil);
  }
  .contact {
    position: absolute;
    left: 336px;
    top: 96px;
    font-size: 13px;
    line-height: 1.45;
    color: var(--foil);
  }
  .contact__name { font-size: 18px; font-weight: 500; line-height: 1.2; }
  .contact__role { font-size: 13px; margin-bottom: 14px; }
  .contact__address { margin-bottom: 12px; }
  .contact__line { display: flex; align-items: center; gap: 6px; }
  .contact__line svg { width: 11px; height: 11px; fill: var(--foil); flex: none; }

  /* Back */
  .back-brand {
    position: absolute;
    inset: 0;
    display: flex;
    align-items: center;
    justify-content: center;
    gap: 18px;
  }
  .back-brand .brand-dot { width: 40px; height: 40px; }
  .back-brand .brand-name { font-size: 32px; line-height: 1.2; }
</style>
</head>
<body>
<div class="canvas">

  <section class="card card--front">
    <div class="front-brand">
      <span class="brand-dot"></span>
      <p class="brand-name">Cedar and Willow<br>Massage Studio</p>
    </div>
    <div class="divider"></div>
    <div class="contact">
      <p class="contact__name">Maya Lindqvist</p>
      <p class="contact__role">Massage Therapist</p>
      <p class="contact__address">2418 Orchard Ave #210<br>Fresno, CA 93721</p>
      <p class="contact__line">
        <svg viewBox="0 0 24 24"><path d="M6.6 10.8a15.1 15.1 0 0 0 6.6 6.6l2.2-2.2c.3-.3.7-.4 1-.2 1.1.4 2.3.6 3.6.6.6 0 1 .4 1 1V20c0 .6-.4 1-1 1A17 17 0 0 1 3 4c0-.6.4-1 1-1h3.5c.6 0 1 .4 1 1 0 1.3.2 2.5.6 3.6.1.3 0 .7-.2 1z"/></svg>
        (559) 555-0187
      </p>
      <p class="contact__line">
        <svg viewBox="0 0 24 24"><path d="M2 5h20v14H2z M2 5l10 8 10-8" fill="none" stroke="currentColor" stroke-width="0"/><path d="M2 5h20v2l-10 7L2 7z"/><path d="M2 9l10 7 10-7v10H2z"/></svg>
        info@cedarandwillow.com
      </p>
      <p class="contact__line">
        <svg viewBox="0 0 24 24"><circle cx="12" cy="12" r="10"/><path d="M2 12h20M12 2c3 3 3 17 0 20M12 2c-3 3-3 17 0 20" fill="none" stroke="#faf9f7" stroke-width="1.6"/></svg>
        www.cedarandwillow.com
      </p>
    </div>
  </section>

  <section class="card card--back">
    <div class="back-brand">
      <span class="brand-dot"></span>
      <p class="brand-name">Cedar and Willow<br>Massage Studio</p>
    </div>
  </section>

</div>
</body>
</html>
```